PHD-project

i need the figures to be in the same stile. info is inside the file. There are 5 figures that need redesign. this is for PhD.

Target Market(s)

it will be used in my phd

Colors

```html
<!DOCTYPE html>
<html lang="en">
<head>
<meta charset="utf-8">
<title>Reflection – Elements and Modes</title>
<link rel="stylesheet" href="https://fonts.googleapis.com/css2?family=Roboto:wght@300;700&display=swap">
<style>
  :root {
    --canvas-bg: #ffffff;
    --core-blue: #4ab0e7;
    --mode-light: #ade0f4;
    --mode-mid: #a1d2ec;
    --mode-deep: #8fbadd;
    --ink: #0a0a0a;
    --body-ink: #1a1a1a;
  }
  html, body {
    margin: 0;
    padding: 0;
    width: 1200px;
    height: 1200px;
    overflow: hidden;
    background: var(--canvas-bg);
  }
  .figure {
    display: block;
    width: 1200px;
    height: 1200px;
  }
  .core-circle { fill: var(--core-blue); opacity: 0.93; }
  .element-bullet { fill: var(--ink); }
  .element-label,
  .mode-label {
    font-family: "Roboto", Arial, sans-serif;
    font-weight: 700;
    font-size: 26px;
    fill: var(--ink);
  }
  .mode-label { text-anchor: middle; }
  .definition {
    font-family: "Roboto", Arial, sans-serif;
    font-weight: 300;
    font-size: 21px;
    fill: var(--body-ink);
  }
</style>
</head>
<body>
<svg class="figure" viewBox="0 0 1200 1200" xmlns="http://www.w3.org/2000/svg" aria-label="Reflection: elements and modes">
  <defs>
    <linearGradient id="mode-gradient" x1="0" y1="0" x2="1" y2="0">
      <stop offset="0.3" stop-color="var(--mode-light)"/>
      <stop offset="0.6" stop-color="var(--mode-mid)"/>
      <stop offset="1" stop-color="var(--mode-deep)"/>
    </linearGradient>
  </defs>

  <g class="modes">
    <circle class="mode-circle mode-circle--on" cx="652" cy="386.4" r="152" fill="url(#mode-gradient)"/>
    <circle class="mode-circle mode-circle--in" cx="664" cy="723.2" r="152" fill="url(#mode-gradient)"/>
  </g>

  <circle class="core-circle" cx="355.2" cy="516" r="281.6"/>

  <g class="elements">
    <circle class="element-bullet" cx="179" cy="416" r="11"/>
    <text class="element-label" x="206" y="426">Reflection involves</text>
    <text class="element-label" x="206" y="461">three elements</text>

    <circle class="element-bullet" cx="179" cy="520" r="11"/>
    <text class="element-label" x="206" y="529">Returing to experience</text>

    <circle class="element-bullet" cx="179" cy="589" r="11"/>
    <text class="element-label" x="206" y="598">Attending to feeling</text>

    <circle class="element-bullet" cx="179" cy="658" r="11"/>
    <text class="element-label" x="206" y="667">Evaluating experience</text>
  </g>

  <g class="mode-labels">
    <text class="mode-label" x="693" y="371">Reflecting</text>
    <text class="mode-label" x="696" y="405">on action</text>
    <text class="mode-label" x="681" y="714">Reflecting</text>
    <text class="mode-label" x="684" y="748">in action</text>
  </g>

  <g class="definition-block">
    <text class="definition" x="805" y="512">Reflection is an active process</text>
    <text class="definition" x="805" y="540">of witnessing one’s can</text>
    <text class="definition" x="805" y="568">experience in order to examine</text>
    <text class="definition" x="805" y="596">it more closely, give meaning to</text>
    <text class="definition" x="805" y="624">it, and learn from it.</text>
  </g>
</svg>
</body>
</html>
```